8 x 8 Social Media Design - Crest Pathway #1

Why be a regular Agent, when you can be a Boss?
MOVA PRIMEX HOMES GROUP
We offer Four Levels of Participation
You Increase your Earning Potential at Each Level
Level One - Learn to Earn Additional Income Through....
Mortgage Originations - Dual Licensing / No Additional Work
Real Estate Investing - Invest Jointly with Us
Agent Recruitment - Up to 10% Override
Level Two - Team Leader
Level Three - Minority Mova Franchise Ownership
Level Four - Majority Mova Franchise Ownership
For more information visit us at www.joinmovaprmx.example and request a meeting with our Managing Broker, Mr. Gordon Talavi.
Look and feel
Each slider illustrates characteristics of the customer's brand and the style your logo design should communicate.

```html
<!DOCTYPE html>
<html lang="en">
<head>
<meta charset="utf-8">
<title>Crest Pathway – Social Post</title>
<link href="https://fonts.googleapis.com/css2?family=Fira+Sans+Condensed:wght@800;900&family=Inter:wght@400;600;700&display=swap" rel="stylesheet">
<style>
  :root{
    --teal:#008d99;
    --teal-deep:#006f79;
    --teal-bright:#00a6b3;
    --accent:#5fc8d3;
    --ink:#161616;
    --white:#ffffff;
  }
  html,body{margin:0;width:1200px;height:1200px;overflow:hidden;background:var(--white);}
  .stage{position:absolute;left:258px;top:258px;width:1100px;height:1100px;transform:scale(0.6218);transform-origin:0 0;overflow:hidden;background:var(--teal);font-family:"Inter",sans-serif;}
  .abs{position:absolute;}
  .dark-block{background:var(--ink);}
  .stripe{position:absolute;background:rgba(255,255,255,.06);transform:skewX(-40deg);}
  .headline{left:252px;color:var(--white);font-family:"Fira Sans Condensed",sans-serif;font-weight:900;text-shadow:3px 3px 0 rgba(0,50,55,.8);margin:0;line-height:1;white-space:nowrap;}
  .headline.small{top:60px;font-size:53px;}
  .headline.big{top:116px;font-size:80px;}
  .crown{left:906px;top:46px;width:122px;height:78px;background:linear-gradient(180deg,rgba(10,10,10,.85),rgba(10,10,10,.55));border-radius:6px;}
  .portrait{position:absolute;left:67px;width:157px;height:157px;background:linear-gradient(160deg,#2a3a3c,#0f1a1b);border:2px solid var(--white);clip-path:polygon(0 0,85% 0,100% 15%,100% 100%,15% 100%,0 85%);}
  .portrait-name{position:absolute;left:45px;width:157px;transform:rotate(-90deg);transform-origin:0 0;color:var(--white);font-weight:700;font-size:13px;line-height:16px;letter-spacing:.3px;text-align:center;white-space:nowrap;}
  .group-photo{background:linear-gradient(180deg,#233134 0%,#1b1f20 55%,#2c2c2c 100%);}
  .group-photo.seated{left:0;top:655px;width:400px;height:430px;border-radius:0 60px 0 0;}
  .group-photo.standing{left:232px;top:530px;width:160px;height:140px;border-radius:70px 70px 0 0;}
  .group-name{left:51px;top:975px;color:var(--white);font-weight:700;font-size:14px;}
  .leg-photo{left:360px;top:225px;width:270px;height:395px;background:linear-gradient(180deg,rgba(70,90,100,0) 0%,#4b5a62 30%,#3a2a22 100%);border-radius:40% 40% 10% 10%/20% 20% 5% 5%;}
  .step{position:absolute;background:linear-gradient(180deg,#6e6e6e 0%,#4a4a4a 60%,var(--ink) 100%);}
  .level-num{position:absolute;color:var(--accent);font-family:"Fira Sans Condensed",sans-serif;font-weight:900;font-size:140px;line-height:1;text-shadow:3px 3px 0 rgba(0,40,45,.6);}
  .level-word{position:absolute;color:var(--white);font-family:"Fira Sans Condensed",sans-serif;font-weight:900;font-size:36px;line-height:30px;transform:rotate(-90deg);transform-origin:0 0;}
  .step-label{position:absolute;color:var(--accent);font-weight:600;font-size:19px;line-height:23px;text-align:center;width:170px;}
  .icon{position:absolute;fill:none;stroke:#e8e8e8;stroke-width:2.2;}
  .income{left:399px;top:760px;color:var(--white);}
  .income h3{margin:0 0 4px;color:var(--accent);font-size:19px;font-weight:600;}
  .income ul{margin:0;padding:0;list-style:none;font-size:18px;line-height:23px;}
  .income li::before{content:"•";color:var(--accent);margin:0 10px 0 2px;}
  .divider{left:706px;top:900px;width:2px;height:155px;background:var(--teal-bright);}
  .contact{right:433px;top:928px;text-align:right;color:var(--white);font-size:18px;line-height:24px;}
  .contact h4{margin:0 0 10px;color:var(--teal-bright);font-size:19px;font-weight:700;}
  .brand{left:740px;top:950px;width:330px;text-align:center;}
  .brand-mark{width:60px;height:60px;background:var(--teal-bright);margin:0 auto 22px;}
  .brand-name{color:var(--white);font-weight:700;font-size:19px;letter-spacing:.5px;white-space:nowrap;}
</style>
</head>
<body>
<div class="stage">
  <div class="stripe" style="left:230px;top:0;width:70px;height:620px;"></div>
  <div class="stripe" style="left:560px;top:0;width:50px;height:320px;"></div>
  <div class="stripe" style="left:760px;top:120px;width:40px;height:260px;"></div>

  <h1 class="abs headline small">Why be a regular Agent,</h1>
  <h1 class="abs headline big">when you can be a Boss?</h1>
  <div class="abs crown" role="img" aria-label="Crown illustration"></div>

  <span class="level-word" style="left:426px;top:612px;">level</span>
  <div class="abs leg-photo" role="img" aria-label="Photo of a man in a suit climbing steps"></div>

  <div class="step" style="left:375px;top:617px;width:725px;height:60px;"></div>
  <div class="step" style="left:569px;top:514px;width:531px;height:163px;"></div>
  <div class="step" style="left:739px;top:412px;width:361px;height:265px;"></div>
  <div class="step" style="left:934px;top:307px;width:166px;height:370px;"></div>
  <div class="abs dark-block" style="left:375px;top:660px;width:725px;height:440px;"></div>
  <div class="abs dark-block" style="left:0;top:825px;width:1100px;height:275px;"></div>

  <span class="level-num" style="left:459px;top:495px;">1</span>
  <span class="level-word" style="left:599px;top:502px;">level</span>
  <span class="level-num" style="left:634px;top:392px;">2</span>
  <span class="level-word" style="left:792px;top:404px;">level</span>
  <span class="level-num" style="left:827px;top:292px;">3</span>
  <span class="level-word" style="left:954px;top:301px;">level</span>
  <span class="level-num" style="left:989px;top:187px;">4</span>

  <svg class="icon" style="left:615px;top:535px;" width="90" height="90" viewBox="0 0 90 90" aria-hidden="true">
    <circle cx="18" cy="20" r="8"/><path d="M4 48c0-10 6-16 14-16s14 6 14 16z"/>
    <circle cx="68" cy="12" r="7"/><path d="M56 36c0-8 5-13 12-13s12 5 12 13z"/>
    <circle cx="68" cy="54" r="7"/><path d="M56 78c0-8 5-13 12-13s12 5 12 13z"/>
    <path d="M34 40h10M44 24v48M44 24h10M44 72h10"/>
  </svg>
  <div class="step-label" style="left:573px;top:630px;">Team<br>Leader</div>

  <svg class="icon" style="left:800px;top:428px;" width="100" height="95" viewBox="0 0 100 95" aria-hidden="true">
    <path d="M30 92L6 46a30 30 0 1 1 48 0z"/><rect x="16" y="20" width="28" height="24"/><path d="M14 22h32M26 44v-10h8v10"/>
    <path d="M60 34h10l6-8h8M60 42h16l6 6h6"/><circle cx="88" cy="26" r="3"/><circle cx="92" cy="48" r="3"/>
  </svg>
  <div class="step-label" style="left:761px;top:527px;">Minority Mova<br>Franchise<br>Ownership</div>

  <svg class="icon" style="left:975px;top:328px;" width="100" height="95" viewBox="0 0 100 95" aria-hidden="true">
    <path d="M30 92L6 46a30 30 0 1 1 48 0z"/><rect x="16" y="20" width="28" height="24"/><path d="M14 22h32M26 44v-10h8v10"/>
    <path d="M60 34h10l6-8h8M60 42h16l6 6h6"/><circle cx="88" cy="26" r="3"/><circle cx="92" cy="48" r="3"/>
  </svg>
  <div class="step-label" style="left:935px;top:422px;">Majority<br>Mova<br>Franchise<br>Ownership</div>

  <svg class="icon" style="left:440px;top:650px;" width="95" height="95" viewBox="0 0 95 95" aria-hidden="true">
    <circle cx="25" cy="24" r="13"/><circle cx="66" cy="42" r="13"/>
    <path d="M25 16v16M29 19h-6a3 3 0 0 0 0 5h4a3 3 0 0 1 0 5h-6"/>
    <path d="M66 34v16M70 37h-6a3 3 0 0 0 0 5h4a3 3 0 0 1 0 5h-6"/>
    <path d="M4 70h14v22H4zM18 74h20l10 6h20l16-10M18 88h40l30-20"/>
  </svg>

  <div class="abs income">
    <h3>Learn to Earn Additional Income Through....</h3>
    <ul>
      <li>Mortgage Originations - Dual Licensing / No Additional Work</li>
      <li>Real Estate Investing - Invest Jointly with Us</li>
      <li>Agent Recruitment - Up to 10% Override</li>
    </ul>
  </div>

  <div class="abs divider"></div>
  <div class="abs contact">
    <h4>REACH US</h4>
    4100 Harlow Ave Ste. 500<br>
    Northbrook, MD 20900<br>
    Office: 301-555-0148
  </div>
  <div class="abs brand">
    <div class="brand-mark"></div>
    <div class="brand-name">MOVA PRIMEX HOMES GROUP</div>
  </div>

  <div class="portrait" style="top:100px;" role="img" aria-label="Portrait of Marcus Dellow"></div>
  <span class="portrait-name" style="top:257px;">MARCUS DELLOW</span>
  <div class="portrait" style="top:287px;" role="img" aria-label="Portrait of Gordon Talavi"></div>
  <span class="portrait-name" style="top:444px;">GORDON TALAVI</span>
  <div class="portrait" style="top:489px;" role="img" aria-label="Portrait of Tunde Aroyo"></div>
  <span class="portrait-name" style="top:646px;">TUNDE AROYO</span>

  <div class="abs group-photo standing" role="img" aria-label="Photo of Owen standing"></div>
  <div class="abs group-photo seated" role="img" aria-label="Photo of Reed seated on a sofa"></div>
  <span class="abs group-name">REED AND OWEN</span>
</div>
</body>
</html>
```